Meadowlark Property Review is a leading provider of residential appraisal and home inspection products in S

I need a business card/logo designed that obviously describes my business. We are a residential appraisal and home inspection company in Springfield, MO. We offer residential appraisals, home inspection, pest inspection and radon gas measurement. We have been in business for 18 years and hold state certified residential appraisal licenses and OBREX certified home inspection licenses. I have a logo that I really like and will attach, but would be open to new suggestions. I like more modern designs than traditional and would like a two sided card with our services, licenses and qualifications on the back.

```html
<!DOCTYPE html>
<html lang="en">
<head>
<meta charset="utf-8">
<title>Meadowlark Property Review – Business Card</title>
<link rel="stylesheet" href="https://fonts.googleapis.com/css2?family=Open+Sans:ital,wght@0,400;0,600;0,700;1,400&display=swap">
<style>
  :root {
    --backdrop: #2e2e2e;
    --backdrop-dark: #1f1f1f;
    --card-white: #ffffff;
    --brand-orange: #f7a21d;
    --brand-orange-deep: #f2931a;
    --brand-brown: #a88756;
    --text-grey: #5a5a5a;
    --rule-grey: #d9d9d9;
  }
  * { box-sizing: border-box; margin: 0; padding: 0; }
  html, body { width: 1200px; height: 659px; overflow: hidden; }
  body {
    background: radial-gradient(ellipse at 50% 45%, var(--backdrop) 0%, var(--backdrop-dark) 100%);
    font-family: "Open Sans", Arial, sans-serif;
    position: relative;
  }
  .card {
    position: absolute;
    top: 192px;
    width: 480px;
    height: 274px;
    overflow: hidden;
    box-shadow: 0 10px 24px rgba(0,0,0,.45);
  }

  /* Front */
  .card-front { left: 85px; background: var(--card-white); }
  .front-edge {
    position: absolute; top: 0; right: 0; width: 18px; height: 100%;
  }
  .front-divider {
    position: absolute; left: 30px; top: 142px; width: 400px; height: 1px;
    background: linear-gradient(90deg, transparent, var(--rule-grey) 30%, var(--rule-grey) 70%, transparent);
  }
  .brand {
    position: absolute; left: 34px; top: 176px;
    display: flex; align-items: center; gap: 12px;
  }
  .brand-square { width: 22px; height: 22px; background: var(--brand-orange); flex: none; }
  .brand-name {
    font-weight: 700; font-size: 21px; line-height: 1.15; color: var(--brand-brown);
    width: 230px;
  }
  .contact {
    position: absolute; left: 250px; top: 26px; width: 200px;
    color: var(--text-grey); font-size: 10.5px; line-height: 1.55;
  }
  .contact-name { font-weight: 600; font-size: 16px; color: var(--brand-brown); line-height: 1.2; }
  .contact-title { color: var(--brand-orange); font-size: 11px; margin-bottom: 6px; }
  .contact-line { display: flex; align-items: center; gap: 7px; white-space: nowrap; }
  .contact-line svg { width: 10px; height: 10px; flex: none; fill: var(--text-grey); }
  .contact-address { margin-bottom: 4px; }

  /* Back */
  .card-back {
    left: 635px;
    background: radial-gradient(ellipse at 60% 40%, var(--brand-orange) 0%, var(--brand-orange-deep) 100%);
    color: var(--card-white);
  }
  .back-mark {
    position: absolute; right: 44px; top: 70px; width: 230px;
    display: flex; align-items: center; gap: 12px;
  }
  .back-mark .brand-square { background: var(--card-white); }
  .back-mark .brand-name { color: var(--card-white); width: auto; font-size: 20px; }
  .services {
    position: absolute; left: 34px; bottom: 34px;
    list-style: none; font-style: italic; font-size: 11.5px; line-height: 1.6;
  }
  .services li::before { content: "• "; }
</style>
</head>
<body>
  <section class="card card-front" aria-label="Business card front">
    <svg class="front-edge" viewBox="0 0 18 274" preserveAspectRatio="none" aria-hidden="true">
      <path d="M18 0 V274 H8 V30 L0 22 L8 14 V0 Z" fill="var(--brand-brown)"/>
    </svg>
    <div class="contact">
      <p class="contact-name">Dana Whitfield</p>
      <p class="contact-title">CEO/Founder</p>
      <p class="contact-address">412 Larkspur Court<br>Springfield, Missouri 65804</p>
      <p class="contact-line">
        <svg viewBox="0 0 10 10"><path d="M2 0.5 L3.8 2.6 L2.9 3.7 Q4 6 6.3 7.1 L7.4 6.2 L9.5 8 L8.4 9.5 Q3.5 9 0.5 1.6 Z"/></svg>417 555 0138</p>
      <p class="contact-line">
        <svg viewBox="0 0 10 10"><rect x="1" y="3" width="8" height="6" rx="1"/><rect x="3" y="0.5" width="4" height="3"/></svg>417 555 0192</p>
      <p class="contact-line">
        <svg viewBox="0 0 10 10"><path d="M0.5 2 H9.5 V8.5 H0.5 Z M1 2.5 L5 5.5 L9 2.5" stroke="#fff" stroke-width=".8"/></svg>dana@meadowlarkreview.com</p>
      <p class="contact-line">
        <svg viewBox="0 0 10 10"><circle cx="5" cy="5" r="4.5"/></svg>www.meadowlarkreview.com</p>
    </div>
    <div class="front-divider"></div>
    <div class="brand">
      <span class="brand-square"></span>
      <span class="brand-name">Meadowlark Property Review</span>
    </div>
  </section>

  <section class="card card-back" aria-label="Business card back">
    <div class="back-mark">
      <span class="brand-square"></span>
      <span class="brand-name">Meadowlark</span>
    </div>
    <ul class="services">
      <li>Residential appraisals</li>
      <li>Home inspection</li>
      <li>Pest inspection</li>
      <li>Radon gas measurement.</li>
    </ul>
  </section>
</body>
</html>
```